SaaS Early tech startup business card design

Unique design for experience ecommerce platform company. the business cards will be used by executive members. conformance with color code is required.

```html
<!DOCTYPE html>
<html lang="en">
<head>
<meta charset="utf-8">
<title>Nuvora business card</title>
<link href="https://fonts.googleapis.com/css2?family=Open+Sans:wght@400;700&display=swap" rel="stylesheet">
<style>
  :root {
    --backdrop: #1c1c1d;
    --brand-blue: #17668f;
    --brand-teal: #1fb99a;
    --paper: #ffffff;
    --ink: #1d2a33;
  }
  * { margin: 0; padding: 0; box-sizing: border-box; }
  html, body { width: 1200px; height: 988px; overflow: hidden; }
  body {
    background: var(--backdrop);
    font-family: "Open Sans", Arial, sans-serif;
    position: relative;
  }
  .card {
    position: absolute;
    width: 640px;
    height: 366px;
    border-radius: 22px;
    overflow: hidden;
  }
  .card-front {
    left: 60px; top: 70px;
    background: var(--brand-blue);
    display: flex; align-items: center; justify-content: center;
  }
  .card-front .wordmark {
    font-weight: 700;
    font-size: 120px;
    letter-spacing: -2px;
    color: var(--brand-teal);
  }
  .card-back {
    left: 500px; top: 560px;
    background: var(--paper);
  }
  .card-back .wave { position: absolute; inset: 0; width: 100%; height: 100%; }
  .card-back .wordmark {
    position: absolute;
    right: 60px; top: 36px;
    font-weight: 700;
    font-size: 62px;
    line-height: 1;
    letter-spacing: -1px;
    color: var(--brand-blue);
  }
  .identity {
    position: absolute;
    left: 0; top: 118px;
    padding-left: 40px;
  }
  .identity::before {
    content: "";
    position: absolute;
    left: 0; top: 6px;
    width: 16px; height: 38px;
    background: var(--brand-blue);
    border-radius: 0 6px 6px 0;
  }
  .identity .name {
    font-weight: 700;
    font-size: 30px;
    line-height: 1.05;
    color: var(--brand-blue);
  }
  .identity .role {
    font-size: 15px;
    color: var(--ink);
  }
  .contact {
    position: absolute;
    left: 262px; top: 250px;
    color: var(--paper);
    font-size: 13px;
    line-height: 1.4;
  }
  .contact .address { margin-bottom: 6px; }
  .contact .line { display: flex; align-items: center; gap: 8px; }
  .contact svg { width: 11px; height: 11px; fill: var(--paper); flex: none; }
</style>
</head>
<body>

<section class="card card-front" aria-label="Card front">
  <span class="wordmark">Nuvora</span>
</section>

<section class="card card-back" aria-label="Card back">
  <svg class="wave" viewBox="0 0 640 366" preserveAspectRatio="none" aria-hidden="true">
    <path d="M134,366 C155,270 210,186 356,180 C496,172 596,156 640,80" fill="none" stroke="var(--brand-teal)" stroke-width="5"/>
    <path d="M150,366 C170,280 220,200 360,192 C500,184 600,170 640,100 L640,366 Z" fill="var(--brand-blue)"/>
  </svg>

  <span class="wordmark">Nuvora</span>

  <div class="identity">
    <p class="name">Daniel Reyes</p>
    <p class="role">Managing Director</p>
  </div>

  <div class="contact">
    <p class="address">18 Harbor Lane,<br>Westfield, Avalon - 40317</p>
    <p class="line">
      <svg viewBox="0 0 24 24"><path d="M6.6 10.8a15.1 15.1 0 0 0 6.6 6.6l2.2-2.2a1 1 0 0 1 1-.25 11.4 11.4 0 0 0 3.6.57 1 1 0 0 1 1 1V20a1 1 0 0 1-1 1A17 17 0 0 1 3 4a1 1 0 0 1 1-1h3.5a1 1 0 0 1 1 1c0 1.250.2 2.45.57 3.57a1 1 0 0 1-.25 1z"/></svg>
      +044 210 5587
    </p>
    <p class="line">
      <svg viewBox="0 0 24 24"><path d="M2 5h20v14H2zm2 2v.5l8 5 8-5V7zm0 3v7h16v-7l-8 5z"/></svg>
      hello@nuvora.io
    </p>
    <p class="line">
      <svg viewBox="0 0 24 24"><circle cx="12" cy="12" r="10"/></svg>
      www.nuvora.io
    </p>
  </div>
</section>

</body>
</html>
```